Buch-/eBook-Cover für Traumatherapeutin
Zielgruppe
Ich bin Traumatherapeutin und schreibe ein Buch zum Thema Trauma bearbeiten.
Meine Zielgruppe sucht Heilung, Genesung, Selbstliebe etc.
Aufgabenstellung
Buchcover
Bitte erstell mir ein modernes positives inspirierendes Buchcover mit dem
Titel: 'Morgenlicht NEU entdecken“
Untertitel: „Spüre den Mut der ganz in dir wohnt“
Dr. Mira Kessow
Ich hätte gerne ein modernes Buch, das entweder einen Bezug zum Thema Trauma hat oder aber einfach stylische Schriftzüge. Bin aber auch offen für andere Vorschläge.
Dunkelblau, weiß und türkis oder auch rosa mag ich ganz gerne. Wobei Dunkelblau, weiß und türkis meine Favoriten sind und mit rosa höchstens kleinere Akzente gesetzt werden sollten.
Das Buchcover soll modern sein und direkt ansprechen. Gerne eine originelle Lösung, oder etwas Besonderes, etwas das Tiefe ausdrückt, oder man mehrmals hinsehen muss um etwas zu erkennen oder etwas das mehr Interpretationsspielraum lässt.
Gerne auch viel weiß, zumindest heller und nicht zu dunkel. Stylish, aber nicht überfrachtet.
Schreib mich gerne an, wenn du Fragen hast.
Ich habe mal zwei Beispiel von Typolösungen angehängt, die ich ganz cool fände.
Ich freue mich auf deine Ideen :-)
Ganz liebe Grüße
Mira

```html
<!DOCTYPE html>
<html lang="de">
<head>
<meta charset="utf-8">
<title>Morgenlicht neu entdecken – Dr. Mira Kessow</title>
<link rel="stylesheet" href="https://fonts.googleapis.com/css2?family=Bebas+Neue&family=Allura&family=Roboto:wght@400&display=swap">
<style>
  :root {
    --teal: #4fb8a6;
    --gold-light: #d3c047;
    --gold-dark: #a58a1b;
    --paper: #ffffff;
    --petal: #e4eaee;
    --disc: #f3a613;
  }
  html, body {
    margin: 0;
    padding: 0;
    overflow: hidden;
    background: var(--paper);
  }
  .cover {
    position: relative;
    width: 750px;
    height: 1200px;
    background: var(--paper);
    overflow: hidden;
  }
  .author {
    position: absolute;
    top: 70px;
    left: 0;
    width: 100%;
    margin: 0;
    text-align: center;
    font-family: "Bebas Neue", sans-serif;
    font-size: 36px;
    letter-spacing: 0.5px;
    color: var(--teal);
    font-weight: 400;
  }
  .title {
    margin: 0;
    font-weight: 400;
  }
  .title-line {
    position: absolute;
    left: 0;
    width: 100%;
    text-align: center;
    font-family: "Bebas Neue", sans-serif;
    color: var(--teal);
    line-height: 1;
  }
  .title-top {
    top: 138px;
    font-size: 150px;
    letter-spacing: 1px;
  }
  .title-bottom {
    top: 445px;
    font-size: 172px;
    letter-spacing: 1px;
  }
  .title-accent {
    position: absolute;
    top: 210px;
    left: 0;
    width: 100%;
    text-align: center;
    font-family: "Allura", cursive;
    font-size: 250px;
    line-height: 1;
    text-transform: lowercase;
    background: linear-gradient(100deg, var(--gold-light) 0%, var(--gold-dark) 40%, var(--gold-light) 60%, var(--gold-dark) 80%, var(--gold-light) 100%);
    -webkit-background-clip: text;
    background-clip: text;
    color: transparent;
  }
  .subtitle {
    position: absolute;
    top: 604px;
    left: 0;
    width: 100%;
    margin: 0;
    text-align: center;
    font-family: "Roboto", sans-serif;
    font-size: 33px;
    font-weight: 400;
    color: var(--teal);
    letter-spacing: 0.3px;
  }
  .flower {
    position: absolute;
    left: 222px;
    top: 712px;
    width: 290px;
    height: 290px;
    border-radius: 50%;
    background: radial-gradient(circle, var(--disc) 0%, var(--disc) 30%, var(--petal) 34%, var(--petal) 80%, rgba(228,234,238,0) 100%);
  }
</style>
</head>
<body>
  <main class="cover">
    <p class="author">Dr. Mira Kessow</p>
    <h1 class="title">
      <span class="title-line title-top">Morgenlicht</span>
      <span class="title-line title-bottom">Entdecken</span>
      <span class="title-accent">NEU</span>
    </h1>
    <p class="subtitle">Spüre den Mut der ganz in dir wohnt</p>
    <div class="flower" role="img" aria-label="Weiße Margeritenblüte mit gelb-orangem Blütenkorb, von oben gesehen"></div>
  </main>
</body>
</html>
```